Premium Business Card for Wealth Creation

Please see attached business card for example.
Happy to look at options like Blue background with Yellow
Target Market(s)
People who want to buy investment property or create wealth
Industry/Entity Type
Investment
Contact Information for Business Card
Tel: 1800 314 579
Mobile: 0417 265 904
Address: Level 1, 64 Carrow Lane Kelmarsh West 4821
Name: Martin Feldway
Title: CEO
Website: www.quolvane.com.au
Email: martin@quolvane.com.au
Font styles to use
Sans Serif
Colors
0255a3
fbed22
Requirements
Must have
- Look great

```html
<!DOCTYPE html>
<html lang="en">
<head>
<meta charset="utf-8">
<title>Quolvane Business Card</title>
<link href="https://fonts.googleapis.com/css2?family=Open+Sans:wght@400;600;700&display=swap" rel="stylesheet">
<style>
  :root {
    --brand-blue: #0255a3;
    --panel-blue-light: #4f78cc;
    --panel-blue-dark: #2f57b8;
    --accent-yellow: #f2d33a;
    --card-white: #f7f7f7;
    --card-shade: #e6e6e6;
    --backdrop: #e9e7e3;
    --ink-white: #ffffff;
  }
  * { box-sizing: border-box; margin: 0; padding: 0; }
  html, body { width: 1200px; height: 780px; overflow: hidden; }
  body {
    background: var(--backdrop);
    font-family: "Open Sans", Arial, sans-serif;
    display: flex;
    align-items: center;
    justify-content: center;
    gap: 48px;
  }
  .card {
    width: 532px;
    height: 304px;
    border-radius: 3px;
    box-shadow: 0 10px 26px rgba(0,0,0,0.18), 0 2px 4px rgba(0,0,0,0.12);
    overflow: hidden;
    position: relative;
  }
  .card--front { display: flex; background: var(--card-white); }
  .front__brand-panel {
    width: 46%;
    background: linear-gradient(160deg, var(--card-white), var(--card-shade));
    display: flex;
    align-items: center;
    justify-content: center;
    border-right: 5px solid var(--accent-yellow);
  }
  .front__info-panel {
    flex: 1;
    background: linear-gradient(150deg, var(--panel-blue-light), var(--panel-blue-dark));
    padding: 34px 24px 0 26px;
    color: var(--ink-white);
  }
  .contact-name { font-size: 20px; font-weight: 700; line-height: 1.1; }
  .contact-title { font-size: 14px; color: var(--accent-yellow); margin-bottom: 16px; }
  .contact-address { font-size: 13px; line-height: 1.35; margin-bottom: 4px; }
  .contact-line { display: flex; align-items: center; gap: 7px; font-size: 13px; line-height: 1.45; margin-top: 2px; }
  .contact-icon {
    width: 15px; height: 15px;
    background: var(--accent-yellow);
    display: flex; align-items: center; justify-content: center;
    flex: none;
  }
  .contact-web { font-size: 13px; color: var(--accent-yellow); margin-top: 8px; }
  .brand-name { font-weight: 600; color: var(--brand-blue); letter-spacing: 0.5px; }
  .brand-name--small { font-size: 32px; }
  .brand-name--large { font-size: 54px; }
  .card--back {
    background: linear-gradient(160deg, var(--card-white), var(--card-shade));
    display: flex; align-items: center; justify-content: center;
  }
</style>
</head>
<body>
  <section class="card card--front">
    <div class="front__brand-panel">
      <span class="brand-name brand-name--small">Quolvane</span>
    </div>
    <div class="front__info-panel">
      <p class="contact-name">Martin Feldway</p>
      <p class="contact-title">CEO</p>
      <p class="contact-address">Level 1, 64 Carrow Lane<br>Kelmarsh West 4821</p>
      <p class="contact-line">
        <span class="contact-icon">
          <svg width="11" height="11" viewBox="0 0 12 12"><path d="M2.5 1h2l1 3-1.5 1a7 7 0 0 0 3 3l1-1.5 3 1v2a1 1 0 0 1-1 1A10 10 0 0 1 1.5 2a1 1 0 0 1 1-1z" fill="var(--panel-blue-dark)"/></svg>
        </span>1800 314 579
      </p>
      <p class="contact-line">
        <span class="contact-icon">
          <svg width="11" height="11" viewBox="0 0 12 12"><rect x="3" y="0.5" width="6" height="11" rx="1" fill="var(--panel-blue-dark)"/><rect x="4" y="2" width="4" height="6" fill="var(--accent-yellow)"/></svg>
        </span>0417 265 904
      </p>
      <p class="contact-line">
        <span class="contact-icon">
          <svg width="11" height="11" viewBox="0 0 12 12"><rect x="0.5" y="2.5" width="11" height="7" fill="var(--panel-blue-dark)"/><path d="M0.5 2.5 6 7l5.5-4.5" fill="none" stroke="var(--accent-yellow)" stroke-width="1"/></svg>
        </span>martin@quolvane.com.au
      </p>
      <p class="contact-web">www.quolvane.com.au</p>
    </div>
  </section>

  <section class="card card--back">
    <span class="brand-name brand-name--large">Quolvane</span>
  </section>
</body>
</html>
```